Web Design Project

Website Design Brief

Company Details
1a) Name of Company

MAPLEHAVEN
1) What is the nature of your business?: Briefly describe your products or services:

INDEPENDENT CONTEMPORARY TRADITIONAL ITALIAN RESTAURANT IN THE HEART OF ELMSWORTH QUAY ALSO CATERING FOR PRIVATE CORPORATE EVENTS AND WEDDING RECEPTIONS

1a) Who is your target market? Who are you hoping to reach with your site?

CITY CORPORATES, LOCAL CORPORATES/BUSINESSES, LOCAL RESIDENTS, VISITORS TO THE DOCK, LOCAL HOTELS

Website Details
1b) Do you have an existing website? If so, what is the URL?
HTTP://WWW.MAPLEHAVENTRATTORIA.EXAMPLE

2b) IMPORTANT: Please list at least 3 URLs (web addresses) of high quality sites that you like the look of (these do not have to be sites who’s business is similar to yours. It aids us in determining what your design style is.) Please consider layout, colours, navigation, graphics, and typography.

http://www.thecorvelle.example/

http://www.dunmorrow.example/

http://www.pavokitchen.example/

http://www.ilfaro.example/

3b) What colours or colour schemes would you like?

WHITE, BLACK, SILVER/ALUMINIUM (PLS LOOK AT OUR OUTSIDE CHAIRS)

4b) List the Navigation links for your Site:

5b) What type of look are you trying to achieve? (e.g. clean, high-tech, conservative, warm, flashy, etc.)

SIMPLE ELEGANT CLASSY INFORMATIVE, EASY TO USE, A REFLECTION OF THE BUSINESS ITSELF

6b) Please provide the addresses of competitors' sites, if possible:

Do not contact the client direct - all questions should go through Brightwell Venues - info@brightwellvenues.example
Updates

thanks for the designs that I have received so far. I have these general comments:

- please avoid using icons for phones or paperclips etc 
- use dummy text (one design used text from another website) 
- there won't any live social media feeds to the site
the client likes a lot of the designs that this company comes up with: 

i look forward to see some more designs

hi all, 

further to my last update, here are a few more pointers:
- there will be no search facilities - so no "search" box please 
- please just use the images supplied - no stock ones
- use just the page names give (no other pages) 

The client is looking for a simple, elegant design. 

Many thanks 
Rolf 

thanks for all the designs. 

I have uploaded another file to the brief which shows some posters that the client particularly likes. Perhaps the homepage could consist of large rectangle made up of a number of boxes - for some introductory text, a large image, mailing list, contact details, Lunch Special etc - just an idea! 
It's clear that the client likes clean lines with square edges. 
I want to be able to pass the designs directly onto the client so can designers avoid adding extra info or page. For example one design has a tab for a "Gift Card" - it will be easier for me if such additions are avoided. 

thanks!                                                                                                                                                                                                                                                                                                                                                                                                    

Thank you for all your designs - please keep them coming! 

hi all,

I am meeting the client tomorrow afternoon so please submit revisions / designs before then. 

Many thanks, 
Rolf

Target Market(s)

Business people, upmarket etc

Industry/Entity Type

Business

Requirements
Must have
• - The home page needs a slide show of images as well as:
- a mailing list form - very simple, "Join our mailing list - name, email"
- 3 or 4 sentences of text
- facebook link

```html
<!DOCTYPE html>
<html lang="en">
<head>
<meta charset="utf-8">
<title>Maplehaven Italian – Contact Us</title>
<link rel="stylesheet" href="https://fonts.googleapis.com/css2?family=Open+Sans:wght@400;600&family=Kaushan+Script&family=Tinos&display=swap">
<style>
  :root {
    --ink: #111;
    --sidebar-dark: #2b2b2b;
    --sidebar-light: #c9c9c9;
    --panel: rgba(222, 222, 222, 0.82);
    --white: #fff;
    --muted: #555;
    --accent: #e8606a;
    --venue-box: #cfcfcf;
    --footer: #000;
    --line: #bdbdbd;
    --button: #3a3a3a;
    --map: #e9e5dc;
  }
  * { box-sizing: border-box; margin: 0; padding: 0; }
  html, body { width: 1200px; height: 771px; overflow: hidden; }
  body { position: relative; font-family: "Open Sans", sans-serif; color: var(--ink); background: #222; }

  .backdrop {
    position: absolute; inset: 0;
    background:
      radial-gradient(ellipse at 70% 70%, #9a8470 0%, rgba(120,100,80,0) 40%),
      radial-gradient(ellipse at 15% 30%, #d8d4cf 0%, rgba(200,200,200,0) 35%),
      radial-gradient(ellipse at 85% 15%, #b8aa98 0%, rgba(150,140,120,0) 40%),
      linear-gradient(180deg, #6e6a66 0%, #4a4542 55%, #2e2a28 100%);
  }

  .sidebar {
    position: absolute; left: 105px; top: 0; width: 272px; height: 707px;
    background: linear-gradient(180deg, var(--sidebar-light) 0%, #8a8a8a 22%, #4a4a4a 48%, var(--sidebar-dark) 60%, rgba(30,30,30,0.75) 100%);
  }
  .brand { position: absolute; top: 22px; left: 0; width: 272px; text-align: center; color: #1a1a1a; }
  .brand-name { font-size: 40px; font-weight: 400; letter-spacing: 1px; }
  .brand-sub { font-size: 15px; letter-spacing: 5px; margin-top: -4px; }

  .main-nav { position: absolute; left: 42px; top: 146px; width: 183px; list-style: none; }
  .main-nav li { height: 44px; border-bottom: 2px solid var(--line); padding: 6px 0 0 22px; }
  .main-nav a { font-family: "Kaushan Script", cursive; font-size: 19px; color: var(--white); text-decoration: none; }
  .main-nav .current a { color: var(--accent); }

  .nav-arrow { position: absolute; top: 326px; width: 42px; height: 42px; z-index: 2; }
  .nav-arrow.prev { left: 84px; }
  .nav-arrow.next { left: 355px; }

  .venue-hire { position: absolute; left: 105px; top: 401px; width: 272px; height: 71px; background: var(--venue-box); }
  .venue-hire h2 { font-weight: 400; font-size: 23px; text-align: center; margin-top: 5px; }
  .venue-hire p { font-family: "Tinos", serif; font-size: 13px; line-height: 14px; margin-left: 106px; color: #222; }

  .locate { position: absolute; left: 127px; top: 500px; width: 244px; color: var(--white); font-size: 11.5px; letter-spacing: .3px; }
  .locate h3 { font-weight: 400; font-size: 19px; display: flex; align-items: flex-end; gap: 6px; margin-bottom: 10px; }
  .locate dl { display: grid; grid-template-columns: 58px 1fr; row-gap: 1px; line-height: 17.5px; }
  .locate dd { white-space: nowrap; }
  .locate .gap { margin-top: 18px; }

  .contact-panel { position: absolute; left: 377px; top: 146px; width: 770px; height: 500px; background: var(--panel); }
  .contact-panel h1 { position: absolute; left: 35px; top: 30px; font-weight: 400; font-size: 22px; }
  .contact-panel .intro { position: absolute; left: 35px; top: 66px; font-size: 17px; color: var(--white); }

  .contact-form { position: absolute; left: 36px; top: 114px; width: 266px; font-size: 13px; color: #333; }
  .contact-form label { display: block; height: 22px; }
  .contact-form .field { display: block; width: 266px; height: 22px; background: var(--white); border: 1px solid #aaa; margin-bottom: 9px; }
  .contact-form .field.comments { height: 50px; }
  .contact-form button {
    display: block; margin: 48px 0 0 44px; width: 169px; height: 24px; border: none;
    background: linear-gradient(180deg, #777 0%, var(--button) 50%, #111 100%);
    color: var(--white); font-family: "Open Sans", sans-serif; font-size: 14px;
  }

  .map { position: absolute; left: 503px; top: 80px; width: 209px; height: 208px; background: linear-gradient(135deg, var(--map), #d9d4c9); }

  .contact-details { position: absolute; left: 503px; top: 306px; font-size: 12.5px; color: #222; }
  .contact-details h3 { display: flex; align-items: center; gap: 10px; font-weight: 400; font-size: 18px; color: var(--muted); margin-bottom: 6px; }
  .contact-details p { margin-left: 38px; line-height: 26px; }

  .site-footer { position: absolute; left: 0; top: 707px; width: 1200px; height: 64px; background: var(--footer); color: var(--white); }
  .follow { position: absolute; left: 111px; top: 24px; font-size: 12px; display: flex; align-items: center; gap: 10px; }
  .follow .social { width: 34px; height: 34px; border-radius: 50%; background: radial-gradient(circle at 40% 35%, #888, #2a2a2a); margin-left: 8px; }
  .follow .social:first-of-type { margin-left: 14px; }
  .copyright { position: absolute; left: 967px; top: 28px; font-size: 12px; }
</style>
</head>
<body>
  <div class="backdrop" role="img" aria-label="Blurred photograph of a plated restaurant dish and table setting"></div>

  <aside class="sidebar">
    <div class="brand">
      <div class="brand-name">Maplehaven</div>
      <div class="brand-sub">ITALIAN</div>
    </div>
    <ul class="main-nav">
      <li><a href="#">Welcome</a></li>
      <li class="current"><a href="#">Our Restaurant</a></li>
      <li><a href="#">Our Menu</a></li>
      <li><a href="#">Gallery</a></li>
      <li><a href="#">Events</a></li>
    </ul>
  </aside>

  <section class="venue-hire">
    <h2>Free Venue Hire</h2>
    <p>Book your next event<br>at Maplehaven Italian</p>
  </section>

  <section class="locate">
    <h3>
      <svg width="22" height="30" viewBox="0 0 22 30" aria-hidden="true"><path d="M11 1C5 1 1 5.5 1 11c0 7 10 18 10 18s10-11 10-18C21 5.5 17 1 11 1z" fill="#3d8fd6"/><circle cx="11" cy="11" r="4" fill="#1d5d99"/></svg>
      Locate Us
    </h3>
    <dl>
      <dt>Address:</dt><dd>18 Harbour Row, City of<br>Elmsworth, EQ4 2TD</dd>
      <dt>Phone:</dt><dd>020 5550 1942</dd>
      <dt>Fax:</dt><dd>(+44) 020 5550 1943</dd>
      <dt class="gap">Email:</dt><dd class="gap">info@maplehaven.example</dd>
      <dt>Website:</dt><dd>www.maplehaven.example</dd>
    </dl>
  </section>

  <main class="contact-panel">
    <h1>Contact Us</h1>
    <p class="intro">Kindly post your valuable Suggestions &amp; Query</p>
    <form class="contact-form">
      <label>Enter your Name</label><span class="field"></span>
      <label>Enter your Email</label><span class="field"></span>
      <label>Enter your Phone Number</label><span class="field"></span>
      <label>Add Your Comments Here:</label><span class="field comments"></span>
      <button type="button">Submit Query</button>
    </form>

    <div class="map" role="img" aria-label="Street map showing the restaurant location"></div>

    <section class="contact-details">
      <h3>
        <svg width="28" height="26" viewBox="0 0 28 26" aria-hidden="true"><rect width="28" height="26" rx="3" fill="#666"/><path d="M9 5c-2 1-3 3-2 6 2 5 6 9 10 10 2 0 4-1 4-3l-3-3-2 2c-2-1-4-3-5-5l2-2-3-4z" fill="#fff"/></svg>
        Contact Details
      </h3>
      <p>#12 Alder Road,Lorem ipsum,</p>
      <p>Phone: +91 555012874</p>
      <p>Tollfree: (006) 55501234</p>
      <p>E-mail: info@alderhall.example</p>
    </section>
  </main>

  <svg class="nav-arrow prev" viewBox="0 0 42 42" aria-label="Previous">
    <circle cx="21" cy="21" r="19" fill="#fff" stroke="#777" stroke-width="2"/>
    <circle cx="21" cy="21" r="14" fill="none" stroke="#222" stroke-width="2.5"/>
    <path d="M28 21H14M20 14l-7 7 7 7" fill="none" stroke="#222" stroke-width="3"/>
  </svg>
  <svg class="nav-arrow next" viewBox="0 0 42 42" aria-label="Next">
    <circle cx="21" cy="21" r="19" fill="#fff" stroke="#777" stroke-width="2"/>
    <circle cx="21" cy="21" r="14" fill="none" stroke="#222" stroke-width="2.5"/>
    <path d="M14 21h14M22 14l7 7-7 7" fill="none" stroke="#222" stroke-width="3"/>
  </svg>

  <footer class="site-footer">
    <div class="follow">
      <span>Folow us on :</span>
      <span class="social" aria-label="Social link"></span>
      <span class="social" aria-label="Social link"></span>
      <span class="social" aria-label="Social link"></span>
      <span class="social" aria-label="Social link"></span>
    </div>
    <p class="copyright">Copyright Al right reserved</p>
  </footer>
</body>
</html>
```